Design a Website in Wordpress for an Australian Health Training Company in Health related courses

We require a WORDPRESS based Website (due to add on's we need to use for third party software) to replace our old site.
We offer national face to face delivery in medical reception, terminology and also administration.
The website will have around 6 pages and the ability to describe our main 6 courses (perhaps on the Courses page this may be tabs opening up to details for example?)
I have attached a previous sample of a Joomla site which was being developed (please do not feel you have to copy this - but I am just giving it as a sample - copying would be boring). But it gives an idea of look/feel and colours which may be suitable. Open to other ideas though.
I will provide some of the content, but would like the ability to finish the content myself.
Images and graphics are important. While a few medical photos re great - don't be tempted to us all pictures of doctors and nurses (although a couple would be good) - these are administrative courses so general corporate, eye catching visionary pictures of people in general are great. A medical type picture is also fine.
THE BOOKING system - will be via an ADD ON which will occur at the end of the project and is supplied by a third party software company (our student management system). This project will include up to 2 hours working with the Tech guys from the third party software to enable the ADD ON. If this ADD ON requires more time, we will pay hourly (although I do not expect it will).
Target Market(s)
Mostly a female market, many mature aged women target 25-45 yrs. Mixture of medical/health and corporate. Maybe a bit of mums returning to work and corporate inspiration.
Industry/Entity Type
It Company
Coding
Coded - Design and coding required
Number of Pages Required
5+ page
Requirements
Must have
- Wordpress
- Great graphics
- Interesting
- professional and clean
- Enquiry section (info Pak)
- Should have a University feel to it - Education
- Pages
- Home Page - About Us - Recruitment -Courses - Class Schedule - Traineeships Queensland Funding - Latest News Blog - Corporate Training- Contact us

```html
<!DOCTYPE html>
<html lang="en">
<head>
<meta charset="utf-8">
<title>Hartwell Institute of Training</title>
<link href="https://fonts.googleapis.com/css2?family=Open+Sans:ital,wght@0,400;0,600;0,700;1,400&family=Raleway:wght@500;600;700&display=swap" rel="stylesheet">
<style>
:root{
  --navy:#2c4466;
  --navy-deep:#243a5a;
  --slate:#3d5579;
  --slate-alt:#354c6f;
  --heading:#3b5273;
  --orange:#f4a23f;
  --orange-deep:#e88f24;
  --text:#4a4a4a;
  --muted:#777;
  --grey-band:#ececec;
  --white:#fff;
  --footer:#3a5378;
  --footer-bottom:#304667;
}
*{margin:0;padding:0;box-sizing:border-box}
html,body{width:1200px;height:2250px;overflow:hidden}
body{position:relative;background:var(--white);font-family:'Open Sans',Arial,sans-serif;color:var(--text)}
.abs{position:absolute}
.topline{left:0;top:0;width:1200px;height:6px;background:var(--navy)}

/* header */
.brand{left:84px;top:22px;width:180px;height:110px;display:flex;flex-direction:column;align-items:center;justify-content:center;gap:8px}
.brand-name{font-family:'Raleway',sans-serif;font-weight:700;font-size:15px;line-height:18px;color:var(--navy);text-align:center;text-transform:uppercase;white-space:nowrap}
.brand-mark{width:40px;height:40px;background:var(--navy)}
.header-tabs{left:900px;top:0;height:27px;display:flex}
.header-tabs span{display:flex;align-items:center;gap:5px;padding:0 14px;font-size:11px;color:var(--white)}
.tab-enrol{background:var(--orange);border-radius:0 0 0 12px}
.tab-info{background:var(--navy);border-radius:0 0 12px 0}
.phone{left:585px;top:63px;display:flex;align-items:center;gap:10px}
.phone-ring{width:39px;height:39px;border:2px solid var(--orange);border-radius:50%;display:flex;align-items:center;justify-content:center}
.phone-num{font-size:21px;color:var(--navy)}
.search{left:780px;top:63px;width:315px;height:40px;display:flex;border:1px solid #d6d6d6;border-radius:3px;overflow:hidden}
.search input{flex:1;border:0;padding:0 12px;font:12px 'Open Sans',sans-serif;color:#666}
.search button{width:43px;border:0;background:var(--orange);display:flex;align-items:center;justify-content:center}

/* navigation */
.mainnav{left:0;top:138px;width:1200px;height:54px;background:linear-gradient(#4a6285,#2f4669)}
.mainnav ul{list-style:none;display:flex;position:absolute;left:99px;top:0;height:54px}
.mainnav li{display:flex;align-items:center;padding:0 13px;font-size:12.5px;color:var(--white);height:54px;white-space:nowrap}
.mainnav li.active{background:var(--orange);padding:0 25px}

/* hero */
.hero{left:0;top:192px;width:1200px;height:460px;background:linear-gradient(100deg,#5c6b82 0%,#9aa3bf 30%,#c9c3dc 50%,#7d8494 75%,#3f4a5a 100%)}
.hero-title{left:162px;top:468px;font-family:'Raleway',sans-serif;font-weight:600;font-size:27px;line-height:29px;color:var(--white);text-transform:uppercase}
.chev{width:16px;height:50px}
.quick{left:802px;top:205px;width:296px;height:343px;background:rgba(38,55,82,.88);padding:0 13px}
.quick h3{font-family:'Raleway',sans-serif;font-weight:600;font-size:19px;color:var(--white);height:50px;line-height:50px;border-bottom:1px solid rgba(255,255,255,.2);margin:0 -13px 12px;padding-left:13px}
.qfield{height:36px;margin-bottom:10px;border:1px solid rgba(255,255,255,.55);display:flex;align-items:center;font-size:12px;color:var(--white)}
.qfield .qi{width:32px;height:100%;display:flex;align-items:center;justify-content:center}
.qfield .caret{margin-left:auto;margin-right:12px;width:0;height:0;border:6px solid transparent;border-top-color:var(--white);margin-top:6px}
.qbtn{width:124px;height:36px;background:var(--orange);color:var(--white);font-size:12px;display:flex;align-items:center;justify-content:center;margin-top:2px}

/* features */
.features{left:99px;top:568px;width:996px;height:244px;display:flex}
.feature{flex:1;display:flex;flex-direction:column;align-items:center;padding-top:20px;text-align:center;background:var(--slate)}
.feature:nth-child(even){background:var(--slate-alt)}
.f-icon{width:96px;height:96px;border-radius:50%;background:var(--white);border:3px solid #c9d0dc;display:flex;align-items:center;justify-content:center}
.feature h4{margin-top:19px;font-family:'Raleway',sans-serif;font-weight:700;font-size:16px;color:var(--white);text-transform:uppercase}
.feature p{margin-top:6px;font-size:12px;line-height:22px;color:#dbe1ea;width:220px}

/* welcome */
.video{left:99px;top:858px;width:402px;height:228px;background:#222;padding:3px;box-shadow:0 8px 14px rgba(0,0,0,.25)}
.video-frame{width:100%;height:190px;background:linear-gradient(110deg,#5f8fae,#9ec5da 40%,#d7e4ea 70%,#7aa0b6)}
.video-bar{height:32px;background:linear-gradient(#3a3a3a,#161616);display:flex;align-items:center;gap:10px;padding:0 10px;font-size:9px;color:#ccc}
.progress{flex:1;height:5px;background:#555;border-radius:3px;position:relative}
.progress i{position:absolute;left:0;top:0;width:48%;height:5px;background:#2b7cc1;border-radius:3px}
.welcome{left:525px;top:856px;width:570px;display:flex;flex-direction:column;align-items:flex-start}
.welcome-title{font-family:'Raleway',sans-serif;font-weight:700;font-size:28px;line-height:28px;color:var(--heading);text-transform:uppercase}
.welcome-text{margin:4px 0 0 3px;width:566px;font-size:11.5px;line-height:20px;color:var(--text);text-align:justify}
.btn-orange{background:linear-gradient(var(--orange),var(--orange-deep));color:var(--white);font-size:12.5px;display:flex;align-items:center;justify-content:center;border-radius:3px}
.welcome-more{margin:6px 0 0 3px;width:104px;height:36px}

/* blog */
.blog-band{left:0;top:1135px;width:1200px;height:469px;background:var(--grey-band)}
.section-title{font-family:'Raleway',sans-serif;font-weight:700;font-size:28px;color:var(--heading);text-transform:uppercase}
.blog-title{left:0;top:1175px;width:1200px;text-align:center}
.post{top:1233px;width:226px;height:330px;background:var(--white);border:1px solid #dcdcdc;padding:4px}
.post-img{height:162px;border:1px solid #ddd}
.post h5{margin:18px 10px 0;font-size:12.5px;font-weight:700;color:#555;text-transform:uppercase}
.post .meta{margin:8px 10px 0;display:flex;align-items:center;gap:6px;font-size:12px;color:#555}
.post p{margin:6px 10px 0;font-size:12px;line-height:21px;color:#555}

/* testimonials & why */
.testi-title{left:117px;top:1662px}
.quote{left:117px;top:1722px;width:500px;font-size:12.5px;line-height:24px;font-style:italic;color:var(--muted)}
.avatar{left:105px;top:1807px;width:88px;height:88px;border-radius:50%;background:linear-gradient(#cfd9e8,#6b88c4);border:3px solid #e4e4e4}
.person{left:213px;top:1838px;font-size:12.5px;line-height:22px;color:#333}
.person b{color:var(--orange-deep);display:block;text-transform:uppercase}
.testi-nav{left:518px;top:1853px;display:flex;gap:3px}
.testi-nav span{width:13px;height:13px;border-radius:50%;background:#999}
.why{left:693px;top:1662px;width:400px;display:flex;flex-direction:column;align-items:flex-start}
.why-text{margin-top:8px;width:400px;font-size:12px;line-height:24px;color:var(--text)}
.why-grid{margin-top:10px;display:grid;grid-template-columns:200px 200px;row-gap:9px;font-size:12.5px;color:var(--text)}
.why-grid div{display:flex;align-items:center;gap:12px}
.why-more{margin-top:12px;font-size:14px;color:var(--orange-deep);text-decoration:underline}

/* footer */
.footer{left:0;top:1938px;width:1200px;height:252px;background:var(--footer)}
.foot-brand{left:97px;top:1988px;width:210px;height:164px;display:flex;flex-direction:column;align-items:center;justify-content:center;gap:12px}
.foot-brand .brand-name{color:var(--white);font-size:16px;line-height:20px}
.foot-brand .brand-mark{background:var(--white)}
.foot-col{top:1978px;color:var(--white)}
.foot-col h6{font-family:'Raleway',sans-serif;font-weight:700;font-size:16px;text-transform:uppercase;margin-bottom:14px}
.foot-links{list-style:none;font-size:12.5px;line-height:27px;padding-left:10px}
.foot-links li::before{content:"› ";}
.chat-row{display:flex;gap:18px;font-size:12.5px;line-height:19px;margin-bottom:18px;padding-left:6px}
.foot-input{width:252px;height:35px;border:1px solid rgba(255,255,255,.3);font-size:12px;color:#dde3ec;padding:0 12px;display:flex;align-items:center;margin-top:14px}
.foot-submit{width:86px;height:33px;margin-top:14px}
.bottombar{left:0;top:2190px;width:1200px;height:60px;background:var(--footer-bottom)}
.copy{left:93px;top:2208px;font-size:12.5px;color:#dde3ec}
.social{left:757px;top:2200px;display:flex;align-items:center;gap:6px;font-size:12.5px;color:#dde3ec}
.social i{width:33px;height:33px;border-radius:50%;display:inline-block}
</style>
</head>
<body>
<div class="abs topline"></div>

<header>
  <div class="abs brand"><div class="brand-name">Hartwell Institute<br>of Training</div><div class="brand-mark"></div></div>
  <div class="abs header-tabs">
    <span class="tab-enrol"><svg width="11" height="11" viewBox="0 0 12 12"><path d="M2 10l1-3 6-6 2 2-6 6z" fill="#fff"/></svg>Enrol Now</span>
    <span class="tab-info"><svg width="11" height="11" viewBox="0 0 12 12"><circle cx="6" cy="6" r="6" fill="#fff"/><rect x="5.2" y="5" width="1.6" height="4.5" fill="#2c4466"/><circle cx="6" cy="3.3" r="1" fill="#2c4466"/></svg>Info Pack</span>
  </div>
  <div class="abs phone">
    <div class="phone-ring"><svg width="18" height="18" viewBox="0 0 24 24"><path d="M6.6 10.8a15 15 0 006.6 6.6l2.2-2.2a1 1 0 011-.25 11.4 11.4 0 003.6.6 1 1 0 011 1V20a1 1 0 01-1 1A17 17 0 013 4a1 1 0 011-1h3.5a1 1 0 011 1 11.4 11.4 0 00.6 3.6 1 1 0 01-.25 1z" fill="#f4a23f"/></svg></div>
    <span class="phone-num">1800 555 014</span>
  </div>
  <div class="abs search"><input value="Enter your keywords..." readonly><button aria-label="Search"><svg width="16" height="16" viewBox="0 0 24 24"><circle cx="10" cy="10" r="6.5" stroke="#fff" stroke-width="3" fill="none"/><path d="M15 15l6 6" stroke="#fff" stroke-width="3"/></svg></button></div>
</header>

<nav class="abs mainnav">
  <ul>
    <li class="active">Home</li><li>About Us</li><li>Recruitment</li><li>Courses</li><li>Class Schedule</li><li style="padding-left:24px">Traineeships Queensland Funding</li><li>Latest News Blog</li><li>Corporate Training</li><li>Contact us</li>
  </ul>
</nav>

<section>
  <div class="abs hero" role="img" aria-label="Photo of a health professional taking a patient's blood pressure in a clinic"></div>
  <h1 class="abs hero-title">Health Training Company<br>in Australia</h1>
  <svg class="abs chev" style="left:40px;top:368px" viewBox="0 0 16 50"><path d="M14 2L2 25l12 23" stroke="#fff" stroke-width="1.5" fill="none"/></svg>
  <svg class="abs chev" style="left:1144px;top:368px" viewBox="0 0 16 50"><path d="M2 2l12 23L2 48" stroke="#fff" stroke-width="1.5" fill="none"/></svg>
  <svg class="abs chev" style="left:40px;top:660px" viewBox="0 0 16 50"><path d="M14 2L2 25l12 23" stroke="#999" stroke-width="1.5" fill="none"/></svg>
  <svg class="abs chev" style="left:1146px;top:660px" viewBox="0 0 16 50"><path d="M2 2l12 23L2 48" stroke="#999" stroke-width="1.5" fill="none"/></svg>

  <form class="abs quick">
    <h3>QUICK CONTACT</h3>
    <div class="qfield"><span class="qi"><svg width="12" height="12" viewBox="0 0 12 12"><circle cx="6" cy="3.5" r="3" fill="#fff"/><path d="M0 12a6 5 0 0112 0z" fill="#fff"/></svg></span>Enter your name</div>
    <div class="qfield"><span class="qi"><svg width="13" height="10" viewBox="0 0 13 10"><rect width="13" height="10" fill="#fff"/><path d="M0 0l6.5 5L13 0" stroke="#354c6f" fill="none"/></svg></span>Email Number</div>
    <div class="qfield"><span class="qi"><svg width="11" height="13" viewBox="0 0 11 13"><rect width="11" height="13" fill="#fff"/><path d="M2 4h7M2 7h7M2 10h5" stroke="#354c6f"/></svg></span>Course<span class="caret"></span></div>
    <div class="qfield"><span class="qi"><svg width="14" height="12" viewBox="0 0 14 12"><path d="M0 0h6v4h8v3l-4 5-3-2-3-3-4-1z" fill="#fff"/></svg></span>State<span class="caret"></span></div>
    <div class="qfield"><span class="qi"><svg width="8" height="13" viewBox="0 0 8 13"><rect width="8" height="13" rx="1.5" fill="#fff"/><rect x="1.2" y="1.5" width="5.6" height="8.5" fill="#354c6f"/></svg></span>Mobile Number</div>
    <div class="qbtn">Enquiry</div>
  </form>
</section>

<section class="abs features">
  <div class="feature">
    <div class="f-icon"><svg width="48" height="48" viewBox="0 0 48 48"><path d="M10 26a14 14 0 0128 0" stroke="#2c4466" stroke-width="4" fill="none"/><rect x="6" y="24" width="8" height="12" rx="3" fill="#2c4466"/><rect x="34" y="24" width="8" height="12" rx="3" fill="#2c4466"/><path d="M38 36q0 6-10 6" stroke="#2c4466" stroke-width="2.5" fill="none"/><path d="M18 17h12v5H18z" fill="#e74c3c"/><path d="M22 13h4v13h-4z" fill="#e74c3c"/></svg></div>
    <h4>Medical Reception</h4><p>Hartwell is Australia's Leading Provider of Educational, Training and Support Services for the Medical</p>
  </div>
  <div class="feature">
    <div class="f-icon"><svg width="48" height="48" viewBox="0 0 48 48"><rect x="6" y="8" width="36" height="26" rx="2" stroke="#2c4466" stroke-width="3" fill="none"/><path d="M20 34l-2 7h12l-2-7M14 42h20" stroke="#2c4466" stroke-width="3" fill="none"/><rect x="12" y="22" width="4" height="8" fill="#2c4466"/><rect x="18" y="17" width="4" height="13" fill="#2c4466"/><rect x="24" y="20" width="4" height="10" fill="#2c4466"/><text x="30" y="27" font-size="11" font-family="Open Sans,sans-serif" font-weight="700" fill="#2c4466">$</text></svg></div>
    <h4>Cert III Business</h4><p>Hartwell is Australia's Leading Provider of Educational, Training and Support Services for the Medical</p>
  </div>
  <div class="feature">
    <div class="f-icon"><svg width="48" height="48" viewBox="0 0 48 48"><rect x="22" y="4" width="22" height="15" rx="3" stroke="#2c4466" stroke-width="2.5" fill="none"/><path d="M27 19l-3 5 7-5" fill="#2c4466"/><path d="M27 10h12M27 14h8" stroke="#2c4466" stroke-width="2"/><rect x="6" y="28" width="24" height="16" rx="6" fill="#2c4466"/><rect x="12" y="16" width="12" height="12" rx="6" fill="#2c4466"/></svg></div>
    <h4>Medical Terminology</h4><p>Hartwell is Australia's Leading Provider of Educational, Training and Support Services for the Medical</p>
  </div>
  <div class="feature">
    <div class="f-icon"><svg width="50" height="40" viewBox="0 0 50 40"><rect x="2" y="6" width="46" height="28" rx="4" stroke="#2c4466" stroke-width="3" fill="none"/><g fill="#2c4466"><rect x="8" y="12" width="5" height="4"/><rect x="15" y="12" width="5" height="4"/><rect x="22" y="12" width="5" height="4"/><rect x="29" y="12" width="5" height="4"/><rect x="36" y="12" width="5" height="4"/><rect x="8" y="19" width="5" height="4"/><rect x="15" y="19" width="5" height="4"/><rect x="22" y="19" width="5" height="4"/><rect x="29" y="19" width="5" height="4"/><rect x="36" y="19" width="5" height="4"/><rect x="13" y="26" width="24" height="4"/></g></svg></div>
    <h4>Keyboard and Typing</h4><p>Hartwell is Australia's Leading Provider of Educational, Training and Support Services for the Medical</p>
  </div>
</section>

<section>
  <div class="abs video">
    <div class="video-frame" role="img" aria-label="Video still of a smiling surgeon in scrubs in an operating theatre"></div>
    <div class="video-bar">
      <svg width="12" height="12" viewBox="0 0 12 12"><path d="M1 0l10 6-10 6z" fill="#fff"/></svg>
      <span>1:38</span><div class="progress"><i></i></div><span>3:12</span>
      <svg width="14" height="12" viewBox="0 0 14 12"><path d="M0 4h3l4-4v12l-4-4H0z" fill="#2b7cc1"/></svg>
      <span style="font-weight:700;font-style:italic">HD</span>
      <svg width="12" height="12" viewBox="0 0 12 12"><path d="M0 4V0h4M8 0h4v4M12 8v4H8M4 12H0V8" stroke="#fff" stroke-width="1.5" fill="none"/></svg>
    </div>
  </div>
  <div class="abs welcome">
    <h2 class="welcome-title">Welcome to Hartwell Institute<br>of Training</h2>
    <p class="welcome-text">Hartwell is Australia Leading Provider of Educational, Training and Support Services for the Medical and Dental industry - enabling students to be immediately skilled and job Ready for a career in Health. Hartwell is a Registered Training Organisation offering specialised Medical Administration Training in over 15 locations Australia wide. Hartwell have trained thousands of students the required knowledge and skills to become successful health care administrators. Hartwell is Australia Leading Provider of Educational, Training and Support Services for the Medical and Dental industry</p>
    <div class="btn-orange welcome-more">Read More</div>
  </div>
</section>

<section>
  <div class="abs blog-band"></div>
  <h2 class="abs section-title blog-title">Latest Blog</h2>
  <article class="abs post" style="left:99px"><div class="post-img" role="img" aria-label="Photo of smiling clinic staff in scrubs" style="background:linear-gradient(120deg,#e9eef2,#9fb6cf 55%,#2f5f96)"></div><h5>The Study Craft Institute</h5><div class="meta"><svg width="13" height="13" viewBox="0 0 13 13"><rect x="0" y="2" width="13" height="11" fill="#555"/><rect x="1.5" y="5" width="10" height="6.5" fill="#fff"/></svg>27 March 2014 <svg style="margin-left:14px" width="15" height="12" viewBox="0 0 15 12"><ellipse cx="7.5" cy="5" rx="7.5" ry="5" fill="#555"/><path d="M3 8l-1 4 5-3z" fill="#555"/></svg>120</div><p>The Study Craft Institute offers you the most advanced and comprehensive online solution to learn available today.</p></article>
  <article class="abs post" style="left:352px"><div class="post-img" role="img" aria-label="Photo of a presenter beside a hand sanitiser station" style="background:linear-gradient(120deg,#b9d0d8,#7fa6b8 45%,#2a8ac4)"></div><h5>The Study Craft Institute</h5><div class="meta"><svg width="13" height="13" viewBox="0 0 13 13"><rect x="0" y="2" width="13" height="11" fill="#555"/><rect x="1.5" y="5" width="10" height="6.5" fill="#fff"/></svg>27 March 2014 <svg style="margin-left:14px" width="15" height="12" viewBox="0 0 15 12"><ellipse cx="7.5" cy="5" rx="7.5" ry="5" fill="#555"/><path d="M3 8l-1 4 5-3z" fill="#555"/></svg>120</div><p>The Study Craft Institute offers you the most advanced and comprehensive online solution to learn available today.</p></article>
  <article class="abs post" style="left:606px"><div class="post-img" role="img" aria-label="Photo of a group of graduates standing in a hospital" style="background:linear-gradient(180deg,#d3d8dc,#9a9fa6 55%,#2d2d33)"></div><h5>The Study Craft Institute</h5><div class="meta"><svg width="13" height="13" viewBox="0 0 13 13"><rect x="0" y="2" width="13" height="11" fill="#555"/><rect x="1.5" y="5" width="10" height="6.5" fill="#fff"/></svg>27 March 2014 <svg style="margin-left:14px" width="15" height="12" viewBox="0 0 15 12"><ellipse cx="7.5" cy="5" rx="7.5" ry="5" fill="#555"/><path d="M3 8l-1 4 5-3z" fill="#555"/></svg>120</div><p>The Study Craft Institute offers you the most advanced and comprehensive online solution to learn available today.</p></article>
  <article class="abs post" style="left:860px"><div class="post-img" role="img" aria-label="Photo of a surgeon working in an operating room" style="background:linear-gradient(120deg,#c9c4de,#8f8fae 50%,#2c3e6a)"></div><h5>The Study Craft Institute</h5><div class="meta"><svg width="13" height="13" viewBox="0 0 13 13"><rect x="0" y="2" width="13" height="11" fill="#555"/><rect x="1.5" y="5" width="10" height="6.5" fill="#fff"/></svg>27 March 2014 <svg style="margin-left:14px" width="15" height="12" viewBox="0 0 15 12"><ellipse cx="7.5" cy="5" rx="7.5" ry="5" fill="#555"/><path d="M3 8l-1 4 5-3z" fill="#555"/></svg>120</div><p>The Study Craft Institute offers you the most advanced and comprehensive online solution to learn available today.</p></article>
</section>

<section>
  <h2 class="abs section-title testi-title">Testimonials</h2>
  <svg class="abs" style="left:98px;top:1712px" width="16" height="14" viewBox="0 0 16 14"><path d="M0 14V8q0-6 6-8v3q-3 1-3 4h3v7zM9 14V8q0-6 6-8v3q-3 1-3 4h3v7z" fill="#ccc"/></svg>
  <p class="abs quote">I completed the course on Feb 13th. Loved it. The trainers, Marla and Jen were excellent in their delivery and knowledge. I want to say a huge thank you for the course and knowledge I came away with. <svg width="16" height="14" viewBox="0 0 16 14" style="vertical-align:-6px"><path d="M16 0v6q0 6-6 8v-3q3-1 3-4h-3V0zM7 0v6q0 6-6 8v-3q3-1 3-4H1V0z" fill="#ccc"/></svg></p>
  <div class="abs avatar" role="img" aria-label="Portrait photo of the student"></div>
  <div class="abs person"><b>Roslyn</b>Manager</div>
  <div class="abs testi-nav"><span></span><span></span></div>

  <div class="abs why">
    <h2 class="section-title">Why Choose Us</h2>
    <p class="why-text">Hartwell is Australia Leading Provider of Educational, Training and Support Services for theMedical and Dental industry - enabling students to be immediately skilled and job Ready for a career</p>
    <div class="why-grid">
      <div><svg width="15" height="15" viewBox="0 0 16 16"><circle cx="8" cy="8" r="8" fill="#f4a23f"/><path d="M4 8l3 3 5-6" stroke="#fff" stroke-width="2" fill="none"/></svg>Quality</div>
      <div><svg width="15" height="15" viewBox="0 0 16 16"><circle cx="8" cy="8" r="8" fill="#f4a23f"/><path d="M4 8l3 3 5-6" stroke="#fff" stroke-width="2" fill="none"/></svg>Value</div>
      <div><svg width="15" height="15" viewBox="0 0 16 16"><circle cx="8" cy="8" r="8" fill="#f4a23f"/><path d="M4 8l3 3 5-6" stroke="#fff" stroke-width="2" fill="none"/></svg>Experience</div>
      <div><svg width="15" height="15" viewBox="0 0 16 16"><circle cx="8" cy="8" r="8" fill="#f4a23f"/><path d="M4 8l3 3 5-6" stroke="#fff" stroke-width="2" fill="none"/></svg>Industry Recognised</div>
      <div><svg width="15" height="15" viewBox="0 0 16 16"><circle cx="8" cy="8" r="8" fill="#f4a23f"/><path d="M4 8l3 3 5-6" stroke="#fff" stroke-width="2" fill="none"/></svg>Great Job Results</div>
    </div>
    <div class="why-more">Read More &gt;&gt;</div>
  </div>
</section>

<footer>
  <div class="abs footer"></div>
  <div class="abs foot-brand"><div class="brand-name">Hartwell Institute<br>of Training</div><div class="brand-mark"></div></div>
  <div class="abs foot-col" style="left:380px">
    <h6>Information</h6>
    <ul class="foot-links"><li>Home</li><li>About Us</li><li>Recruitment</li><li>Courses</li><li>Class Schedule</li><li>Traineeships</li></ul>
  </div>
  <div class="abs foot-col" style="left:592px">
    <h6>Let's Chat!</h6>
    <div class="chat-row"><svg width="10" height="14" viewBox="0 0 10 14"><path d="M5 0a5 5 0 015 5c0 4-5 9-5 9S0 9 0 5a5 5 0 015-5z" fill="#fff"/><circle cx="5" cy="5" r="2" fill="#3a5378"/></svg><span>New South Wales,<br>Victoria &amp; ACT,<br>Western Australia</span></div>
    <div class="chat-row"><svg width="13" height="10" viewBox="0 0 13 10"><rect width="13" height="10" fill="#fff"/><path d="M0 0l6.5 5L13 0" stroke="#3a5378" fill="none"/></svg><span>info@hartwellhealth.example</span></div>
    <div class="chat-row" style="font-size:15px"><svg width="12" height="12" viewBox="0 0 24 24"><path d="M6.6 10.8a15 15 0 006.6 6.6l2.2-2.2a1 1 0 011-.25 11.4 11.4 0 003.6.6 1 1 0 011 1V20a1 1 0 01-1 1A17 17 0 013 4a1 1 0 011-1h3.5a1 1 0 011 1 11.4 11.4 0 00.6 3.6 1 1 0 01-.25 1z" fill="#fff"/></svg><span>1800 555 014</span></div>
  </div>
  <div class="abs foot-col" style="left:843px">
    <h6>Contact Details</h6>
    <p style="font-size:12.5px;line-height:20px;padding-left:5px">Register Your email address to get<br>information about us</p>
    <div class="foot-input">Email address...</div>
    <div class="btn-orange foot-submit">Submit</div>
  </div>
  <div class="abs bottombar"></div>
  <div class="abs copy">© hartwellhealth 2016. All rights reserved</div>
  <div class="abs social">Connect with our social network :&nbsp;<i style="background:#4a6db0"></i><i style="background:#3fa6e0"></i><i style="background:#2f78b3"></i><i style="background:#f4a23f"></i></div>
</footer>
</body>
</html>
```